Fitness Equipment & Service

I want to make the card eye catching and fun. We are called Corvane Motion Limited and we are based in Wales. We sell, install and service all types of fitness equipment from Skipping ropes, right through the Dumbbells, Kettle bells and Barbells through to state of the art Treadmills, Running Machines and Strength Equipment. We also design and install changing room furniture and lockers.

TYPOGRAPHY
We would like to use Futrura. Futura has an appearance of efficiency and forwardness. The typeface is derived
from simple geometric forms (near-perfect circles, triangles and squares) and is based on strokes of
near-even weight, which are low in contrast. This is most visible in the almost perfectly round stroke of
the o, which is nonetheless slightly ovoid.
The lowercase has tall ascenders, which rise above the cap line. The uppercase
characters present proportions similar to those of classical Roman capitals.

TYPOGRAPHIC CONSIDERATIONS
No Strike though
No Horizontal Scaling
No Drop Shadows
No Effects
Never use less than 120% Leading

OUR CORPORATE COLOURS
BRAND GUIDELINES
We were thinking that our primary colour palette consists of the Acid Green (Pantone 382) and Process Black.

We work closely with tquarly Ltd and would like to include their name on the card somewhere. I have attached images of the other brands that we work with as an idea or the small icons I have included that illustrate what we do?. I have very kindly been given permission to use any of the images off the files that I have included below, so I hope these help. I will include these below. I would be open to suggestions if it made the card more striking Can you do it?
Updates

Hi All, Just wanted to add a few thoughts but you are the guys with the creative visions (thats why are here) We are based in Wales, UK and we would be open to lots of different ideas on a theme but must be eye catching, Bold and FUN. If you can or think that the Welsh or any dragon could be put in there then go for it (its not a must have) We have also added some ideas for colour but again its over to you!! GO FOR IT ! Thanks and look forward to your visions! Owen

Hi All, Just thought I would sen through the contact details that need to be on the card. (if you want to play around with icons instead of the wording twitter, Facebook, go for it): Corvane Motion Limited Owen Pritchard Managing Director Mob: +44 (0)7582 913 406 e-mail: sales@corvanemotion.co.uk Web: Corvanemotion.co.uk twitter: @motionLetterbin Facebook: Corvane Motion Limited

```html
<!DOCTYPE html>
<html lang="en">
<head>
<meta charset="utf-8">
<title>Corvane Motion Limited – Business Card</title>
<link rel="stylesheet" href="https://fonts.googleapis.com/css2?family=Jost:wght@400;500&display=swap">
<style>
  :root {
    --page: #8e8f8f;
    --navy-top: #1d5aa6;
    --navy-bottom: #0c2357;
    --card-edge: #0d1a3a;
    --gold: #d9a43a;
    --white: #ffffff;
    --paper: #e9eaee;
    --ink: #17244a;
    --tile-navy: #1d3b5e;
    --tile-sky: #41a2d8;
    --tile-mid: #2a7cb8;
    --tile-deep: #163150;
    --tile-steel: #7f9cb6;
    --tile-slate: #8ba3b8;
    --tile-ocean: #2470a8;
    --tile-night: #111f33;
  }
  * { margin: 0; padding: 0; box-sizing: border-box; }
  html, body { width: 1105px; height: 1200px; overflow: hidden; }
  body {
    background: var(--page);
    font-family: "Jost", "Futura", sans-serif;
    position: relative;
  }
  .card {
    position: absolute;
    left: 172px;
    width: 760px;
    height: 434px;
    border: 2px solid var(--card-edge);
    overflow: hidden;
  }
  /* Front */
  .card--front { top: 120px; }
  .front__backdrop {
    position: absolute; inset: 0;
    background: linear-gradient(180deg, var(--navy-top) 0%, #143f85 45%, var(--navy-bottom) 100%);
  }
  .front__person { position: absolute; left: 43px; top: 32px; }
  .person__name {
    color: var(--gold);
    font-size: 30px; font-weight: 500; letter-spacing: 0.5px;
    line-height: 1.2;
  }
  .person__role { color: var(--white); font-size: 20px; font-weight: 400; line-height: 1.3; }
  .front__address {
    position: absolute; left: 43px; top: 176px;
    color: var(--white); font-size: 18px; line-height: 1.4; font-style: normal;
  }
  .contact-list {
    position: absolute; left: 43px; top: 244px;
    list-style: none;
    color: var(--white); font-size: 18px; line-height: 1.3;
  }
  .contact-list li { display: flex; align-items: center; height: 29px; }
  .contact-list svg { width: 16px; height: 16px; margin-right: 13px; flex: none; }
  .front__brand {
    position: absolute; right: 40px; top: 40px; bottom: 40px; width: 270px;
    display: flex; flex-direction: column; align-items: center; justify-content: center;
    gap: 22px;
  }
  .brand-dot {
    width: 46px; height: 46px; border-radius: 50%;
    background: var(--gold);
  }
  .brand-name {
    color: var(--gold);
    font-size: 34px; font-weight: 500; line-height: 1.2; text-align: center;
    text-transform: uppercase; letter-spacing: 1px;
  }

  /* Back */
  .card--back { top: 640px; display: flex; background: var(--paper); }
  .back__identity {
    width: 324px; height: 100%;
    display: flex; flex-direction: column; align-items: center; justify-content: center;
    gap: 26px;
  }
  .identity__disc {
    width: 150px; height: 150px; border-radius: 50%;
    background: radial-gradient(circle at 45% 40%, #2c5ea5, #0f2456);
  }
  .identity__name {
    color: var(--ink);
    font-size: 24px; font-weight: 500; line-height: 1.2; text-align: center;
    text-transform: uppercase;
  }
  .service-grid {
    flex: 1;
    display: grid;
    grid-template-columns: repeat(4, 1fr);
    grid-template-rows: repeat(4, 1fr);
    gap: 3px;
    background: var(--paper);
    padding-left: 3px;
  }
  .tile { width: 100%; height: 100%; }
  .tile--navy { background: var(--tile-navy); }
  .tile--sky { background: var(--tile-sky); }
  .tile--mid { background: var(--tile-mid); }
  .tile--deep { background: var(--tile-deep); }
  .tile--steel { background: var(--tile-steel); }
  .tile--slate { background: var(--tile-slate); }
  .tile--ocean { background: var(--tile-ocean); }
  .tile--night { background: linear-gradient(160deg, #1b3556, var(--tile-night)); }
  .tile--partner {
    grid-column: span 2;
    background: linear-gradient(160deg, #1c3b60, #0f2340);
    display: flex; flex-direction: column; align-items: center; justify-content: center;
    gap: 4px;
    color: var(--white);
  }
  .partner__name { font-size: 30px; font-weight: 500; line-height: 1.2; letter-spacing: 1px; }
  .partner__tagline { font-size: 12px; font-weight: 400; letter-spacing: 0.5px; line-height: 1.2; }
</style>
</head>
<body>

<section class="card card--front">
  <div class="front__backdrop" role="img" aria-label="Deep blue gradient with a faint world map"></div>

  <div class="front__person">
    <h1 class="person__name">OWEN PRITCHARD</h1>
    <p class="person__role">Managing Director</p>
  </div>

  <address class="front__address">
    2316 Hollins Row<br>
    Kettering Vale, Brynmor 48215
  </address>

  <ul class="contact-list">
    <li>
      <svg viewBox="0 0 16 16"><rect x="4" y="1" width="8" height="14" rx="1.5" fill="none" stroke="#d9a43a" stroke-width="1.6"/><rect x="7" y="12" width="2" height="1.4" fill="#d9a43a"/></svg>
      +44 (0)7582 913 406
    </li>
    <li>
      <svg viewBox="0 0 16 16"><rect x="1" y="3" width="14" height="10" fill="#d9a43a"/><path d="M1 3l7 6 7-6" fill="none" stroke="#0c2357" stroke-width="1.2"/></svg>
      sales@corvanemotion.co.uk
    </li>
    <li>
      <svg viewBox="0 0 16 16"><circle cx="8" cy="8" r="6.5" fill="none" stroke="#d9a43a" stroke-width="1.6"/><ellipse cx="8" cy="8" rx="2.8" ry="6.5" fill="none" stroke="#d9a43a" stroke-width="1.2"/><line x1="1.5" y1="8" x2="14.5" y2="8" stroke="#d9a43a" stroke-width="1.2"/></svg>
      Corvanemotion.co.uk
    </li>
    <li>
      <svg viewBox="0 0 16 16"><rect x="1" y="1" width="14" height="14" fill="#d9a43a"/></svg>
      @motionLetterbin
    </li>
    <li>
      <svg viewBox="0 0 16 16"><rect x="1" y="1" width="14" height="14" fill="#d9a43a"/></svg>
      Corvane Motion Limited
    </li>
  </ul>

  <div class="front__brand">
    <div class="brand-dot"></div>
    <p class="brand-name">Corvane<br>Motion<br>Limited</p>
  </div>
</section>

<section class="card card--back">
  <div class="back__identity">
    <div class="identity__disc"></div>
    <p class="identity__name">Corvane Motion<br>Limited</p>
  </div>

  <div class="service-grid">
    <div class="tile tile--navy" role="img" aria-label="Online services icon"></div>
    <div class="tile tile--sky" role="img" aria-label="Floor plan design icon"></div>
    <div class="tile tile--mid" role="img" aria-label="Treadmill icon"></div>
    <div class="tile tile--deep" role="img" aria-label="Heart rate icon"></div>

    <div class="tile tile--navy" role="img" aria-label="Lockers icon"></div>
    <div class="tile tile--night" role="img" aria-label="Weight plate icon"></div>
    <div class="tile tile--sky" role="img" aria-label="Card terminal icon"></div>
    <div class="tile tile--night" role="img" aria-label="Boxing gloves icon"></div>

    <div class="tile tile--partner">
      <span class="partner__name">TQUARLY</span>
      <span class="partner__tagline">KEEPING GYMS IN MOTION</span>
    </div>
    <div class="tile tile--steel" role="img" aria-label="Kettlebell icon"></div>
    <div class="tile tile--ocean" role="img" aria-label="Stopwatch icon"></div>

    <div class="tile tile--slate" role="img" aria-label="Group training icon"></div>
    <div class="tile tile--ocean" role="img" aria-label="Weight bench icon"></div>
    <div class="tile tile--sky" role="img" aria-label="Delivery van icon"></div>
    <div class="tile tile--night" role="img" aria-label="Exercise bike icon"></div>
  </div>
</section>

</body>
</html>
```